Calmcrest Coach website development

Need a website designed for a coaching business. Very high-end, luxury, professionalism, in the area of STRESS, see brief attached. I have a logo already
Updates

Slow in providing feedback

Target Market(s)

CEOs very successful men and wealthy females, high end luxury market

Industry/Entity Type

coaching

Number of Pages Required

1 page

Requirements
Must have
• Luxury look, professional, serious but warm, appealing to both sexes

```html
<!DOCTYPE html>
<html lang="en">
<head>
<meta charset="utf-8">
<title>Calmcrest Coach — Lifestyle Coaching</title>
<link rel="stylesheet" href="https://fonts.googleapis.com/css2?family=Oswald:wght@400;500;600&family=Poppins:ital,wght@0,400;0,500;0,600;1,400&display=swap">
<style>
:root{
  --ink:#1d1b1c;
  --text:#2f2f2f;
  --muted:#555;
  --topbar:#6a6a6a;
  --light:#e4e4e4;
  --white:#ffffff;
  --line:#222;
  --head:'Oswald',sans-serif;
  --body:'Poppins',sans-serif;
}
*{box-sizing:border-box;margin:0;padding:0}
html,body{width:1200px;height:4431px;overflow:hidden}
body{position:relative;background:var(--white);font-family:var(--body);color:var(--text)}
.abs{position:absolute}
.btn{position:absolute;display:flex;align-items:center;justify-content:center;background:var(--ink);color:var(--white);font-family:var(--head);font-weight:500;font-size:18px;letter-spacing:.3px;text-transform:uppercase;text-decoration:none}
.title{position:absolute;font-family:var(--head);font-weight:400;text-transform:uppercase;color:var(--ink);font-size:38px;letter-spacing:.3px;line-height:1}
.title.center{left:0;width:1200px;text-align:center}
.rule{position:absolute;height:2px;width:118px;background:var(--ink)}
.copy{position:absolute;font-size:14.5px;line-height:32.5px;color:var(--text)}
.photo{position:absolute}

/* top bar */
.topbar{left:0;top:0;width:1200px;height:60px;background:var(--topbar)}
.topbar .contact{position:absolute;top:19px;color:var(--white);font-size:16px;display:flex;align-items:center;gap:10px}
.topbar .contact b{font-weight:600}

/* header */
.brand{position:absolute;left:70px;top:12px;width:190px;text-align:center}
.brand .mark{width:64px;height:64px;margin:0 auto 14px;border-radius:50%;background:var(--ink)}
.brand .name{font-family:var(--head);font-weight:500;font-size:22px;letter-spacing:4px;color:var(--ink);line-height:1}
.brand .tag{font-size:9px;letter-spacing:2.5px;color:var(--muted);margin-top:4px}
.nav{position:absolute;top:114px;right:74px;display:flex;gap:37px;font-size:14px;font-weight:600;color:var(--ink)}
.nav .dot{position:absolute;left:12px;top:-28px;width:14px;height:14px;border-radius:50%;background:var(--ink)}

/* hero */
.hero-title{position:absolute;left:0;width:1200px;top:325px;text-align:center;font-family:var(--head);font-weight:600;font-size:80px;line-height:1.04;color:var(--ink)}
.arrow{position:absolute}

/* hexes */
.hex{position:absolute;width:250px;height:286px}
.hex span{position:absolute;left:0;width:250px;top:124px;text-align:center;font-family:var(--head);font-weight:600;font-size:34px;color:var(--white);letter-spacing:.5px}

/* reviews */
.reviews{left:0;top:2615px;width:1200px;height:525px;background:var(--ink)}
.review{position:absolute;width:315px}
.review p{font-style:italic;font-size:14.5px;line-height:28.5px;color:#d9d9d9}
.review .who{position:absolute;top:190px;left:0;display:flex;align-items:center;gap:20px}
.review .avatar{width:70px;height:70px;border-radius:50%;background:linear-gradient(#c9b3a2,#8c7a70)}
.review .nm{font-family:var(--head);font-size:18px;color:var(--white)}
.review .loc{font-size:13px;color:#bbb}

/* blog */
.post-title{position:absolute;font-family:var(--head);font-size:26px;line-height:36px;color:var(--ink);text-transform:uppercase;width:512px}

/* footer */
.fhead{position:absolute;top:4055px;font-family:var(--head);font-weight:500;font-size:21px;color:var(--white)}
.flist{position:absolute;top:4100px;list-style:none;font-size:14.5px;line-height:37px;color:#d6d6d6}
.faddr{position:absolute;left:588px;top:4100px;font-size:14.5px;color:#d6d6d6;line-height:26px}
.faddr .row{display:flex;gap:16px;margin-bottom:10px}
.faddr svg{flex:none;margin-top:6px}
.email{position:absolute;left:886px;top:4128px;width:240px;height:46px;background:var(--white);font-size:14px;font-weight:500;color:var(--ink);padding:13px 16px}
.sub{position:absolute;left:886px;top:4185px;width:240px;height:44px;background:#3a3839;color:var(--white);font-family:var(--head);font-weight:500;font-size:18px;display:flex;align-items:center;justify-content:center}
.social{position:absolute;left:886px;top:4287px;display:flex;gap:20px}
.social i{width:20px;height:20px;border-radius:50%;background:var(--white);display:block}
.copyright{position:absolute;left:0;top:4350px;width:1200px;height:81px;border-top:1px solid #333;background:#151314;color:#cfcfcf;font-size:14px;text-align:center;padding-top:32px}
</style>
</head>
<body>

<!-- top bar -->
<div class="abs topbar">
  <div class="contact" style="left:680px">
    <svg width="16" height="16" viewBox="0 0 24 24"><path fill="#fff" d="M6.6 10.8a15 15 0 0 0 6.6 6.6l2.2-2.2c.3-.3.7-.4 1-.2 1.1.4 2.3.6 3.6.6.6 0 1 .4 1 1V20c0 .6-.4 1-1 1A17 17 0 0 1 3 4c0-.6.4-1 1-1h3.5c.6 0 1 .4 1 1 0 1.3.2 2.5.6 3.6.1.3 0 .7-.2 1z"/></svg>
    <b>1-800-555-0142</b>
  </div>
  <div class="contact" style="left:874px">
    <svg width="16" height="14" viewBox="0 0 24 20"><path fill="#fff" d="M2 2h20v16H2z"/><path fill="none" stroke="#6a6a6a" stroke-width="2" d="M2 3l10 8 10-8"/></svg>
    hello@calmcrestcoach.com
  </div>
</div>

<!-- header -->
<div class="brand">
  <div class="mark"></div>
  <div class="name">CALMCREST COACH</div>
  <div class="tag">LIFESTYLE COACHING</div>
</div>
<nav class="nav">
  <span style="position:relative">HOME<i class="dot"></i></span>
  <span>ABOUT</span><span>WHAT WE DO</span><span>BLOG</span><span>TESTISMONIALS</span><span>CONTACT US</span>
</nav>

<!-- hero -->
<div class="photo" role="img" aria-label="Smiling woman holding a coffee cup and a man in glasses, bright office" style="left:0;top:160px;width:1200px;height:640px;background:linear-gradient(90deg,#c9a188 0%,#e9ddd3 30%,#f1efee 50%,#a9bfd3 72%,#6f8fb0 100%)"></div>
<svg class="abs" style="left:0;top:700px" width="1200" height="110"><polygon points="0,18 600,100 1200,18 1200,110 0,110" fill="#fff"/></svg>
<div class="hero-title">HEAD COACH<br>GET IT!</div>
<a class="btn" style="left:394px;top:506px;width:192px;height:64px">MEN CLICK HERE</a>
<a class="btn" style="left:616px;top:506px;width:194px;height:64px">WOMEN CLICK HERE</a>
<svg class="arrow" style="left:60px;top:415px" width="24" height="42"><path d="M20 2 3 21l17 19" fill="none" stroke="#1d1b1c" stroke-width="3"/></svg>
<svg class="arrow" style="left:1116px;top:415px" width="24" height="42"><path d="M4 2l17 19L4 40" fill="none" stroke="#1d1b1c" stroke-width="3"/></svg>
<div class="abs" style="left:578px;top:784px;width:44px;height:44px;border-radius:50%;background:var(--ink);border:4px solid #fff"></div>

<!-- welcome -->
<h2 class="title center" style="top:880px">WELCOME TO CALMCREST COACH</h2>
<div class="rule" style="left:541px;top:936px"></div>
<div class="photo" role="img" aria-label="Team meeting around a white table in front of a green plant wall" style="left:74px;top:990px;width:513px;height:368px;background:linear-gradient(180deg,#4e6a3b 0%,#6f7d5d 40%,#d7d5d2 70%,#b9b6b3 100%)"></div>
<p class="copy" style="left:616px;top:980px;width:515px">Calmcrest Coach came about due to my desire to help people lead a better and healthier life. Initially, I was involved in the fitness/body side of health. As years passed and my experience grew, I realized how important the mind was in total wellness, and that the mind is all powerful and controlling. Control the mind, control the body and achieve success. Stress can be the most debilating factor in our lives, it is the root cause of so many diseases and costs the US workplace an estimated 300 billion dollars due to loss of productivity.</p>
<a class="btn" style="left:616px;top:1295px;width:164px;height:63px">READ MORE</a>

<!-- what we do -->
<svg class="abs" style="left:0;top:1430px" width="1200" height="615"><polygon points="0,0 1200,0 1200,615 0,615 0,0 600,96 1200,0" fill="#e4e4e4"/><polygon points="0,0 600,96 1200,0" fill="#fff"/></svg>
<h2 class="title" style="left:74px;top:1612px">WHAT WE DO</h2>
<div class="rule" style="left:74px;top:1668px"></div>
<p class="copy" style="left:74px;top:1692px;width:510px">Sed ut perspiciatis unde omnis iste natus error sit voluptatem accusantium doloremque laudantium, totam rem aperiam, eaque ipsa quae ab illo inventore veritatis et quasi architecto beatae vitae dicta sunt explicabo. Nemo enim ipsam voluptatem quia voluptas sit aspernatur aut odit aut fugit, sed quia consequuntur magni.</p>
<a class="btn" style="left:74px;top:1908px;width:165px;height:64px">READ MORE</a>

<div class="hex" role="img" aria-label="Woman meditating in a dark room" style="left:615px;top:1612px">
  <svg width="250" height="286"><polygon points="125,3 247,73 247,213 125,283 3,213 3,73" fill="#2b2a33" stroke="#fff" stroke-width="5"/></svg><span>YOGA</span>
</div>
<div class="hex" role="img" aria-label="Aromatherapy oil burner with candle" style="left:878px;top:1612px">
  <svg width="250" height="286"><defs><linearGradient id="ga" x1="0" y1="0" x2="0" y2="1"><stop offset="0" stop-color="#7a6a60"/><stop offset="1" stop-color="#b98a5c"/></linearGradient></defs><polygon points="125,3 247,73 247,213 125,283 3,213 3,73" fill="url(#ga)" stroke="#fff" stroke-width="5"/></svg><span>AROMATHERAPY</span>
</div>
<div class="hex" role="img" aria-label="Man with raised arms outdoors in sunlight" style="left:746px;top:1832px">
  <svg width="250" height="286"><defs><linearGradient id="gw" x1="0" y1="0" x2="0" y2="1"><stop offset="0" stop-color="#d7d9dc"/><stop offset="1" stop-color="#7d7a63"/></linearGradient></defs><polygon points="125,3 247,73 247,213 125,283 3,213 3,73" fill="url(#gw)" stroke="#fff" stroke-width="5"/></svg><span>WELLNESS</span>
</div>

<!-- why choose -->
<div class="photo" role="img" aria-label="Businesswoman meditating calmly at her office desk" style="left:74px;top:2177px;width:513px;height:366px;background:linear-gradient(90deg,#3d5872 0%,#8fa4b6 45%,#b9c3cc 70%,#4f6f8e 100%)"></div>
<h2 class="title" style="left:616px;top:2185px">WHY CHOOSE CALMCREST COACH</h2>
<div class="rule" style="left:616px;top:2241px"></div>
<p class="copy" style="left:616px;top:2262px;width:510px">Sed ut perspiciatis unde omnis iste natus error sit voluptatem accusantium doloremque laudantium, totam rem aperiam, eaque ipsa quae ab illo inventore veritatis et quasi architecto beatae vitae dicta sunt explicabo.</p>
<p class="copy" style="left:616px;top:2392px;width:510px">Nemo enim ipsam voluptatem quia voluptas sit aspernatur aut odit aut fugit, sed quia consequuntur magni dolores.</p>
<a class="btn" style="left:616px;top:2470px;width:164px;height:63px">READ MORE</a>

<!-- reviews -->
<section class="abs reviews">
  <h2 class="title center" style="top:72px;color:#fff">CUSTOMER REVIEWS</h2>
  <svg class="arrow" style="left:40px;top:298px" width="16" height="28"><path d="M14 2 3 14l11 12" fill="none" stroke="#fff" stroke-width="2.5"/></svg>
  <svg class="arrow" style="left:1140px;top:298px" width="16" height="28"><path d="M2 2l11 12L2 26" fill="none" stroke="#fff" stroke-width="2.5"/></svg>
  <div class="review" style="left:74px;top:172px">
    <p>“ Sed ut perspiciatis unde omnis iste natus error sit voluptatem accusantium doloremque laudantium, totam rem aperiam, eaque ipsa quae ab illo inventore veritatis et quasi architecto beatae vitae dicta sunt..”</p>
    <div class="who"><i class="avatar" role="img" aria-label="Customer portrait"></i><div><div class="nm">NAME HEADING</div><div class="loc">Location</div></div></div>
  </div>
  <div class="review" style="left:434px;top:172px">
    <p>“ Sed ut perspiciatis unde omnis iste natus error sit voluptatem accusantium doloremque laudantium, totam rem aperiam, eaque ipsa quae ab illo inventore veritatis et quasi architecto beatae vitae dicta sunt..”</p>
    <div class="who"><i class="avatar" role="img" aria-label="Customer portrait"></i><div><div class="nm">NAME HEADING</div><div class="loc">Location</div></div></div>
  </div>
  <div class="review" style="left:796px;top:172px">
    <p>“ Sed ut perspiciatis unde omnis iste natus error sit voluptatem accusantium doloremque laudantium, totam rem aperiam, eaque ipsa quae ab illo inventore veritatis et quasi architecto beatae vitae dicta sunt..”</p>
    <div class="who"><i class="avatar" role="img" aria-label="Customer portrait"></i><div><div class="nm">NAME HEADING</div><div class="loc">Location</div></div></div>
  </div>
</section>

<!-- blog -->
<h2 class="title center" style="top:3197px">LATEST BLOG POSTS</h2>
<div class="rule" style="left:541px;top:3252px"></div>
<div class="photo" role="img" aria-label="Two women in conversation during a coaching session" style="left:74px;top:3290px;width:513px;height:273px;background:linear-gradient(90deg,#6c5f56 0%,#b7a99c 45%,#3e3a3a 75%,#2a2627 100%)"></div>
<div class="photo" role="img" aria-label="Colleagues meeting at a table with laptops" style="left:616px;top:3290px;width:512px;height:273px;background:linear-gradient(180deg,#c8c9c9 0%,#8f8d8a 50%,#2d2c2e 100%)"></div>
<h3 class="post-title" style="left:74px;top:3598px">NEMO ENIM IPSAM VOLUPTATEM QUIA VOLUPTAS SIT ASPERNATUR</h3>
<h3 class="post-title" style="left:616px;top:3598px">NEMO ENIM IPSAM VOLUPTATEM QUIA VOLUPTAS SIT ASPERNATUR</h3>
<p class="copy" style="left:74px;top:3672px;width:510px;line-height:29.5px">Sed ut perspiciatis unde omnis iste natus error sit voluptatem accusantium doloremque laudantium, totam rem aperiam, eaque ipsa quae ab illo inventore veritatis.</p>
<p class="copy" style="left:616px;top:3672px;width:510px;line-height:29.5px">Sed ut perspiciatis unde omnis iste natus error sit voluptatem accusantium doloremque laudantium, totam rem aperiam, eaque ipsa quae ab illo inventore veritatis.</p>
<a class="btn" style="left:74px;top:3775px;width:165px;height:64px">READ MORE</a>
<a class="btn" style="left:616px;top:3775px;width:164px;height:64px">READ MORE</a>

<!-- footer -->
<svg class="abs" style="left:0;top:3888px" width="1200" height="462"><polygon points="0,0 600,76 1200,0 1200,462 0,462" fill="#1d1b1c"/></svg>
<div class="abs" style="left:576px;top:3946px;width:48px;height:48px;border-radius:50%;background:var(--ink);border:4px solid #fff"></div>

<div class="fhead" style="left:74px">SITE MAP</div>
<ul class="flist" style="left:74px"><li>Home</li><li>About</li><li>What We Do</li><li>Blog</li><li>Testimonials</li><li>Contact Us</li></ul>
<div class="fhead" style="left:305px">SERVICES</div>
<ul class="flist" style="left:305px"><li>Sed ut perspiciatis</li><li>Unde omnis iste</li><li>Natus error sit voluptatem</li><li>Accusantium</li><li>Doloremque laudantium</li></ul>
<div class="fhead" style="left:588px">ADDRESS</div>
<div class="faddr">
  <div class="row"><svg width="14" height="18" viewBox="0 0 14 18"><path fill="#fff" d="M7 0a7 7 0 0 0-7 7c0 5 7 11 7 11s7-6 7-11a7 7 0 0 0-7-7zm0 10a3 3 0 1 1 0-6 3 3 0 0 1 0 6z"/></svg><span>14 Linden Row, Elmbridge,<br>Surrey KT9 4ZZ</span></div>
  <div class="row"><svg width="14" height="14" viewBox="0 0 24 24"><path fill="#fff" d="M6.6 10.8a15 15 0 0 0 6.6 6.6l2.2-2.2c.3-.3.7-.4 1-.2 1.1.4 2.3.6 3.6.6.6 0 1 .4 1 1V20c0 .6-.4 1-1 1A17 17 0 0 1 3 4c0-.6.4-1 1-1h3.5c.6 0 1 .4 1 1 0 1.3.2 2.5.6 3.6.1.3 0 .7-.2 1z"/></svg><span>1-800-555-0142</span></div>
  <div class="row"><svg width="14" height="12" viewBox="0 0 24 20"><path fill="#fff" d="M2 2h20v16H2z"/><path fill="none" stroke="#1d1b1c" stroke-width="2" d="M2 3l10 8 10-8"/></svg><span>hello@calmcrestcoach.com</span></div>
</div>
<div class="fhead" style="left:886px">SUBSCRIBE EMAIL</div>
<div class="email">Email Address</div>
<div class="sub">SUBSCRIBE</div>
<div class="fhead" style="left:886px;top:4240px">FOLLOW US</div>
<div class="social" aria-label="Social media links"><i></i><i></i><i></i><i></i><i></i></div>

<div class="copyright">Copyright © 2022. Calmcrest Coach All rights reserved.</div>

</body>
</html>
```